Business Card Design for Occupational Medicine Start Up Company

We need to design a professional business card. We are a healthcare company providing occupational medicine services to blue collar industries. We are professional, efficient and high quality service providers.

Target Market(s)

Blue Collar Industry: Shipbuilding, Ports, Trucking Companies; The Executives and Safety Officers for these companies

Industry/Entity Type

Healthcare

Contact Information for Business Card

Logo, Name, Title, Email, Phone

Other font styles liked:
• Please match our Brand Guide

Requirements
Must have
• Our Company Colors and Logo

```html
<!DOCTYPE html>
<html lang="en">
<head>
<meta charset="utf-8">
<title>CrewCare Clinics – Business Card</title>
<link rel="stylesheet" href="https://fonts.googleapis.com/css2?family=Montserrat:wght@400;500;700&display=swap">
<style>
  :root {
    --backdrop: #2b2b2b;
    --card-light: #ececec;
    --navy: #2b3580;
    --orange: #f5a623;
    --ink-grey: #5a5a5a;
    --rule-grey: #8a8a8a;
    --white: #ffffff;
  }
  * { margin: 0; padding: 0; box-sizing: border-box; }
  html, body {
    width: 1200px;
    height: 1107px;
    overflow: hidden;
    background: var(--backdrop);
    font-family: "Montserrat", sans-serif;
  }
  .stage {
    position: relative;
    width: 1200px;
    height: 1107px;
  }
  .card {
    position: absolute;
    left: 236px;
    width: 803px;
    height: 460px;
    box-shadow: 0 6px 18px rgba(0,0,0,0.45);
  }
  .card-front { top: 69px; background: var(--card-light); }
  .card-back { top: 578px; background: var(--navy); }

  /* brand lockup */
  .brand {
    position: absolute;
    display: flex;
    flex-direction: column;
    align-items: center;
    font-weight: 700;
    text-transform: uppercase;
    line-height: 1;
  }
  .brand-dot { border-radius: 50%; }
  .card-front .brand { right: 43px; top: 56px; color: var(--navy); }
  .card-front .brand-dot { width: 48px; height: 48px; background: var(--navy); margin-bottom: 12px; }
  .card-front .brand-name { font-size: 21px; letter-spacing: 0.5px; }
  .card-front .brand-sub { font-size: 13px; letter-spacing: 4px; margin-top: 3px; }

  .card-back .brand { left: 0; right: 0; top: 138px; color: var(--white); }
  .card-back .brand-dot { width: 68px; height: 68px; background: var(--white); margin-bottom: 42px; }
  .card-back .brand-name { font-size: 40px; letter-spacing: 0.5px; }
  .card-back .brand-sub { font-size: 21px; letter-spacing: 7px; margin-top: 8px; }

  /* person */
  .person-name {
    position: absolute;
    left: 47px;
    top: 214px;
    font-size: 26px;
    font-weight: 500;
    color: var(--navy);
  }
  .person-name .surname { color: var(--orange); }
  .person-title {
    position: absolute;
    left: 47px;
    top: 255px;
    font-size: 15px;
    color: var(--ink-grey);
  }
  .title-rule {
    position: absolute;
    left: 142px;
    top: 266px;
    width: 616px;
    height: 1px;
    background: var(--rule-grey);
  }

  /* contacts */
  .contact-list {
    position: absolute;
    left: 47px;
    top: 341px;
    list-style: none;
    font-size: 16px;
    color: var(--ink-grey);
  }
  .contact-list li {
    display: flex;
    align-items: center;
    height: 27px;
  }
  .contact-list svg {
    width: 14px;
    height: 14px;
    margin-right: 14px;
    fill: var(--navy);
  }
  .contact-list .web-accent { color: var(--orange); }

  .address {
    position: absolute;
    right: 43px;
    top: 361px;
    text-align: right;
    font-style: normal;
    font-size: 16px;
    line-height: 27px;
    color: var(--ink-grey);
  }
</style>
</head>
<body>
<main class="stage">
  <section class="card card-front">
    <div class="brand">
      <span class="brand-dot"></span>
      <span class="brand-name">CrewCare</span>
      <span class="brand-sub">Clinics</span>
    </div>

    <h1 class="person-name">Nadia <span class="surname">Corven</span></h1>
    <p class="person-title">Directeur</p>
    <div class="title-rule"></div>

    <ul class="contact-list">
      <li>
        <svg viewBox="0 0 24 24" aria-hidden="true"><path d="M6.6 10.8a15.1 15.1 0 0 0 6.6 6.6l2.2-2.2c.3-.3.7-.4 1-.2 1.1.4 2.3.6 3.6.6.6 0 1 .4 1 1V20c0 .6-.4 1-1 1A17 17 0 0 1 3 4c0-.6.4-1 1-1h3.5c.6 0 1 .4 1 1 0 1.3.2 2.5.6 3.6.1.3 0 .7-.2 1z"/></svg>
        +0212 0600 555 014
      </li>
      <li>
        <svg viewBox="0 0 24 24" aria-hidden="true"><path d="M2 5h20v14H2z M3 6l9 7 9-7" /></svg>
        n.corven@crewmail.ma
      </li>
      <li>
        <svg viewBox="0 0 24 24" aria-hidden="true"><circle cx="12" cy="12" r="10"/><path d="M2 12h20M12 2c3 3 3 17 0 20M12 2c-3 3-3 17 0 20" stroke="#ececec" stroke-width="1.5" fill="none"/></svg>
        www.<span class="web-accent">corvenhealth</span>.ma
      </li>
    </ul>

    <address class="address">
      PO BOX 50872 Larchwood<br>
      Edmonton, AB T5X-0Q
    </address>
  </section>

  <section class="card card-back">
    <div class="brand">
      <span class="brand-dot"></span>
      <span class="brand-name">CrewCare</span>
      <span class="brand-sub">Clinics</span>
    </div>
  </section>
</main>
</body>
</html>
```